Business Card for a mobile physiotherapy company

I need a layout for a business card for a mobile physiotherapy company.
Slogan is "Mobile Physiotherapy - Your Road To Recovery"
Phone number is 867-555-0142
Email VardenTherapy@postnest.ca (subject to change with website)
Website www.VardenTherapy.ca
My name and credentials: Luke Varden Luke Varden, BSc(kin), MPT, CAFCI, IMS
Information maybe included: Direct Billing, Services including Physiotherapy, IMS, acupuncture
Maybe include facebook and instagram logos
One side with the logo clean and sharp
Other side with details, try not to look too busy, keep everything concise

```html
<!DOCTYPE html>
<html lang="en">
<head>
<meta charset="utf-8">
<title>Varden Therapy – Business Card</title>
<link rel="stylesheet" href="https://fonts.googleapis.com/css2?family=Quattrocento:wght@400;700&display=swap">
<style>
  :root {
    --page-bg: #d9d6d0;
    --card-bg: #eeebe5;
    --navy: #2c4a6e;
    --teal: #1d5a55;
    --ink: #2c4560;
    --light-text: #eef1f3;
    --muted-text: #d2dbe0;
    --deco-top: #3a5a80;
    --deco-bottom: #c9d2d9;
  }
  * { margin: 0; padding: 0; box-sizing: border-box; }
  html, body {
    width: 1200px; height: 1054px; overflow: hidden;
    background: var(--page-bg);
    font-family: "Quattrocento", Georgia, serif;
  }
  .card {
    position: absolute; left: 100px; top: 227px;
    width: 1000px; height: 600px;
    background: var(--card-bg);
    border-radius: 6px;
    overflow: hidden;
    box-shadow: 0 8px 30px rgba(0,0,0,0.15);
  }
  .card-shapes { position: absolute; inset: 0; }
  .wordmark {
    position: absolute; left: 60px; top: 86px;
    display: flex; align-items: center; gap: 20px;
    color: var(--ink); font-weight: 400;
    font-size: 44px; line-height: 1;
  }
  .wordmark-square { width: 40px; height: 40px; background: var(--navy); }
  .holder { position: absolute; left: 47px; top: 244px; color: var(--light-text); }
  .holder-name { font-size: 46px; font-weight: 700; letter-spacing: 1px; line-height: 1; }
  .holder-credentials { font-size: 22px; color: var(--muted-text); margin-top: 14px; }
  .contact-list { position: absolute; left: 60px; top: 366px; list-style: none; color: var(--light-text); }
  .contact-list li { display: flex; align-items: center; height: 36px; font-size: 26px; }
  .contact-list svg { width: 22px; height: 22px; margin-right: 18px; fill: var(--light-text); }
  .tagline { position: absolute; left: 47px; top: 546px; font-size: 24px; color: var(--ink); }
  .follow { position: absolute; left: 717px; top: 546px; display: flex; align-items: center; font-size: 24px; color: var(--ink); }
  .follow .dot { width: 28px; height: 28px; border-radius: 50%; margin-left: 10px; }
  .follow .dot-one { background: var(--navy); margin-left: 8px; }
  .follow .dot-two { background: var(--teal); }
</style>
</head>
<body>
  <div class="card">
    <svg class="card-shapes" width="1000" height="600" viewBox="0 0 1000 600">
      <defs>
        <linearGradient id="bandFill" x1="0" y1="0" x2="1" y2="0">
          <stop offset="0" stop-color="#2c4a6e"/>
          <stop offset="1" stop-color="#1d5a55"/>
        </linearGradient>
        <linearGradient id="decoFill" x1="0" y1="0" x2="0" y2="1">
          <stop offset="0" stop-color="#3a5a80"/>
          <stop offset="1" stop-color="#c9d2d9"/>
        </linearGradient>
      </defs>
      <polygon class="info-band" points="0,214 720,214 447,511 0,511" fill="url(#bandFill)"/>
      <polygon class="brand-decoration" role="img" aria-label="Large brand mark decoration area"
               points="800,150 1000,150 1000,511 480,511" fill="url(#decoFill)" opacity="0.85"/>
    </svg>

    <div class="wordmark">
      <span class="wordmark-square"></span>
      <span class="wordmark-name">Varden Therapy</span>
    </div>

    <div class="holder">
      <h1 class="holder-name">LUKE VARDEN</h1>
      <p class="holder-credentials">BSc(kin), MPT, CAFCI, IMS</p>
    </div>

    <ul class="contact-list">
      <li><svg viewBox="0 0 24 24" aria-hidden="true"><path d="M4 9c0-3 3-5 8-5s8 2 8 5v2h-4V9c-1-1-7-1-8 0v2H4z"/><path d="M6 13h12l2 7H4z"/></svg>867-555-0142</li>
      <li><svg viewBox="0 0 24 24" aria-hidden="true"><path d="M2 5h20v14H2z M3.5 6.5 12 13l8.5-6.5" stroke="#2c4a6e" stroke-width="1.5"/></svg>VardenTherapy@postnest.ca</li>
      <li><svg viewBox="0 0 24 24" aria-hidden="true"><circle cx="12" cy="12" r="10"/><path d="M2 12h20M12 2v20M5 6c4 2 10 2 14 0M5 18c4-2 10-2 14 0" stroke="#2c4a6e" stroke-width="1.4" fill="none"/></svg>www.VardenTherapy.ca</li>
    </ul>

    <p class="tagline">Mobile Physiotherapy - Your Road To Recovery</p>
    <div class="follow">Follow us on:<span class="dot dot-one"></span><span class="dot dot-two"></span></div>
  </div>
</body>
</html>
```